Velmo Swinger site - new website, blogsite and merchandise point, connection to tradeva

We are a well established Swingers Club in the North east of UK and already have an existing site. www.velmo-example.co.uk, BUT we have changed our logo and our information on the site needs to be updated.

We are changing our hosting site to Nimbrashost.example ,also wanting to start a blog which is linked to the club, plus we wish to sell a small exclusive range of Velmo linked merchandise which will also be available on Tradeva.

I have attached a pdf of the majority of the content. additionally we will provide pictures and a videoclip which should be able to be viewed by pc's, lap tops and mobile phones (the whole website must be fully accessible via phone).

The new site must be able to be updated by someone with medium computer knowledge (usually me), by no means expert. Updates will generally be new pictures and written information. The site must be able to be transferred to NimbrasHost.

Velmo is one of the countries leading clubs and emphasises friendliness, fun & safety for its members, we look after you to ensure your experience is the best we can offer. We are very proud of our reputation, built up over more than 10 years.

Target Market(s)

Swingers, dreamers & fantasists, alternative lifestyle people

Coding

Coded - Design and coding required

Number of Pages Required

5+ page

Font styles to use
Sans Serif

Colors
000000
ec1f27
fbfbfb
eeeeee
eaeaea

Requirements
Must have
• website with blog attached, link to tradeva & quidlo, ability to run videoclip and picture album and must be compatable to transfer easily to Nimbrashost and be updated by non-professional (who can learn)
• Straightforward & easy to navigate
• over 18 content page with enter button
Nice to have
• sexy site
• link to chirpster maybe
• black site would be nice with red or white writing
Should not have
• children and animals in anyway shape or form

```html
<!DOCTYPE html>
<html lang="en">
<head>
<meta charset="utf-8">
<title>Velmo – Swingers Club</title>
<link rel="stylesheet" href="https://fonts.googleapis.com/css2?family=Roboto:wght@300;400;500;700;900&family=Open+Sans:wght@400;600&display=swap">
<style>
:root{
  --black:#000000;
  --red:#ec1f27;
  --red-deep:#c4141b;
  --white:#fbfbfb;
  --light:#eeeeee;
  --light-2:#eaeaea;
  --dark:#1c1c1c;
  --dark-2:#232323;
  --grey-text:#bdbdbd;
  --body-text:#555555;
}
*{box-sizing:border-box;margin:0;padding:0}
html,body{width:1200px;height:3232px;overflow:hidden}
body{background:var(--dark);color:var(--white);font-family:"Open Sans",Arial,sans-serif;position:relative}
section,header,footer,.bottom-bar{position:relative;width:1200px;overflow:hidden}
.abs{position:absolute}
.brand{font-family:"Roboto",Arial,sans-serif;font-weight:300;letter-spacing:6px;color:var(--white);text-transform:uppercase}
a{color:inherit;text-decoration:none}

/* hero */
.hero{height:672px}
.hero-photo{position:absolute;inset:0;background:radial-gradient(ellipse at 70% 45%,#a8604a 0%,#6a3424 30%,#3a1c14 60%,#1a0c08 100%)}
.hero-logo{left:97px;top:44px;font-size:64px;line-height:1}
.call{left:657px;top:46px;display:flex;align-items:center;gap:12px;font-family:"Roboto",sans-serif;font-size:17px}
.call-icon{width:26px;height:26px;border-radius:50%;background:var(--red);display:flex;align-items:center;justify-content:center}
.search{left:883px;top:46px;width:216px;height:30px;border-radius:15px;background:var(--white);color:#999;font-size:11px;padding:7px 18px}
.nav{left:457px;top:102px;width:643px;display:flex;justify-content:space-between;font-family:"Roboto",sans-serif;font-size:13.5px;font-weight:500;text-transform:uppercase}
.hero-title{left:97px;top:318px;font-family:"Roboto",sans-serif;font-weight:500;font-size:44px;text-transform:uppercase}
.hero-title span{color:var(--red)}
.hero-text{left:97px;top:384px;width:400px;font-size:14px;line-height:21px;font-weight:600}
.btn{display:inline-flex;align-items:center;justify-content:center;background:var(--red);color:var(--white);font-family:"Roboto",sans-serif;text-transform:uppercase;border-radius:20px}
.hero-btn{left:97px;top:441px;width:108px;height:32px;font-size:12px}
.arrow{top:365px}

/* welcome */
.welcome{height:646px;background:var(--dark-2)}
.welcome h1{position:absolute;top:70px;width:100%;text-align:center;font-family:"Roboto",sans-serif;font-weight:900;font-size:42px}
.welcome h1 span{color:var(--red)}
.welcome-text{position:absolute;top:138px;left:150px;width:900px;text-align:center;font-size:12.5px;line-height:21px}
.feature{position:absolute;top:244px;width:298px;height:298px;border-radius:50%;background:var(--white);color:var(--body-text);text-align:center;padding:40px 38px 0}
.feature.is-red{background:var(--red);color:var(--white)}
.feature h3{font-family:"Roboto",sans-serif;font-weight:400;font-size:16px;text-transform:uppercase;color:#333;margin:16px 0 12px}
.feature.is-red h3{color:var(--white)}
.feature p{font-size:11.5px;line-height:19px}
.feature .more{display:block;margin-top:14px;font-family:"Roboto",sans-serif;font-size:13.5px;color:var(--red);text-transform:uppercase}
.feature.is-red .more{color:var(--white)}

/* about */
.about{height:595px}
.about-bg{position:absolute;inset:0;background:linear-gradient(180deg,#b8141a 0%,#e02028 45%,#a80f14 100%)}
.about-card{position:absolute;left:144px;top:93px;width:910px;height:410px;background:var(--white);box-shadow:0 10px 30px rgba(0,0,0,.35);display:flex}
.about-photo{width:362px;height:100%;background:radial-gradient(ellipse at 50% 60%,#c97a3a 0%,#7a3216 50%,#3a140a 100%)}
.about-body{padding:34px 34px;color:var(--body-text);flex:1}
.about-body h2{font-family:"Roboto",sans-serif;font-weight:400;font-size:20px;color:#333;text-transform:uppercase;margin-bottom:16px;white-space:nowrap}
.about-body p{font-size:11.5px;line-height:21px}
.about-body h4{font-family:"Roboto",sans-serif;font-weight:500;font-size:13px;color:#333;margin:12px 0 8px}
.facilities{display:grid;grid-template-columns:140px 150px 190px;row-gap:6px;font-size:11.5px;list-style:none;white-space:nowrap}
.facilities li::before{content:"";display:inline-block;width:6px;height:6px;border:1.5px solid #333;border-radius:50%;margin-right:12px}
.about-btn{margin-top:22px;width:124px;height:34px;font-size:12px}

/* blog and products */
.news{height:587px;background:var(--dark)}
.news h2{position:absolute;font-family:"Roboto",sans-serif;font-weight:400;font-size:28px;text-transform:uppercase}
.post{position:absolute;left:101px;display:flex;gap:26px}
.post-photo{width:186px;height:147px;border:3px solid var(--white)}
.post h3{font-family:"Roboto",sans-serif;font-weight:400;font-size:16px;margin-bottom:14px}
.post .date{font-size:11px;text-transform:uppercase;margin-bottom:8px}
.post p{font-size:11.5px;line-height:19px;width:260px}
.post .more{font-size:12px;color:var(--red);margin-top:10px;display:block}
.product{position:absolute;left:655px;top:143px;width:444px;height:340px;border:3px solid var(--light-2);background:linear-gradient(90deg,#4a2a18,#7a4a2a 50%,#4a2a18)}
.shirt{position:absolute;left:132px;top:36px;width:180px;height:250px;background:var(--light);border-radius:30px 30px 8px 8px;text-align:center;color:#777;padding-top:76px}
.shirt .brand{color:#555;font-size:24px;letter-spacing:3px}
.shirt p{font-size:10px;line-height:14px;padding:10px 36px}
.shop-btn{width:118px;height:30px;font-size:11px}
.market{position:absolute;left:22px;bottom:16px;font-family:"Roboto",sans-serif;font-weight:700;font-size:30px;color:var(--white)}

/* price */
.price{height:362px}
.price-bg{position:absolute;inset:0;background:linear-gradient(180deg,rgba(236,31,39,.95),rgba(200,20,30,.92)),radial-gradient(circle at 80% 50%,#ff6a5a,#a8101a)}
.price h2{position:absolute;top:104px;width:100%;text-align:center;font-family:"Roboto",sans-serif;font-weight:700;font-size:34px;text-transform:uppercase}
.price p{position:absolute;top:152px;left:280px;width:640px;text-align:center;font-size:13px;line-height:22px;font-weight:600}
.email{left:280px;top:222px;width:472px;height:43px;background:var(--white);color:#999;font-size:12px;padding:13px 14px}
.join{left:765px;top:222px;width:155px;height:43px;background:#1f1f1f;display:flex;align-items:center;justify-content:center;font-family:"Roboto",sans-serif;font-size:14px;text-transform:uppercase}

/* footer */
.site-footer{height:316px;background:var(--dark)}
.site-footer h5{position:absolute;top:58px;font-family:"Roboto",sans-serif;font-weight:400;font-size:18px;text-transform:uppercase}
.links{position:absolute;left:97px;top:108px;list-style:none;font-size:12px;line-height:23px}
.links li::before{content:"›";margin-right:16px}
.contact{position:absolute;left:316px;top:110px;font-size:12px;line-height:20px}
.contact div{display:flex;gap:14px;margin-bottom:14px}
.footer-logo{left:316px;top:242px;font-size:40px;line-height:1}
.quote-text{left:634px;top:102px;width:470px;font-size:11.5px;line-height:19px}
.field{position:absolute;height:42px;border:1px solid var(--white);font-size:11px;padding:13px 12px}
.signup{position:absolute;left:877px;top:200px;width:224px;height:42px;background:var(--red);display:flex;align-items:center;justify-content:center;font-family:"Roboto",sans-serif;font-size:14px;text-transform:uppercase}
.bottom-bar{height:54px;background:var(--dark);border-top:1px solid #333}
.copy{left:97px;top:18px;font-size:11.5px}
.social{right:100px;top:14px;display:flex;gap:8px}
.social span{width:24px;height:24px;border-radius:50%;border:1.5px solid var(--grey-text)}
</style>
</head>
<body>

<header class="hero">
  <div class="hero-photo" role="img" aria-label="Photo of a couple embracing in a warm, dimly lit club interior"></div>
  <div class="abs brand hero-logo">Velmo</div>
  <div class="abs call">
    <span class="call-icon"><svg width="13" height="13" viewBox="0 0 24 24"><path fill="#fbfbfb" d="M6.6 10.8a15.1 15.1 0 0 0 6.6 6.6l2.2-2.2c.3-.3.7-.4 1-.2 1.1.4 2.3.6 3.6.6.6 0 1 .4 1 1V20c0 .6-.4 1-1 1A17 17 0 0 1 3 4c0-.6.4-1 1-1h3.5c.6 0 1 .4 1 1 0 1.3.2 2.5.6 3.6.1.3 0 .7-.2 1z"/></svg></span>
    Call us : 01632 960418
  </div>
  <div class="abs search">search</div>
  <nav class="abs nav">
    <a>Home</a><a>Diary</a><a>Theme Parties</a><a>TV/TG and Admirers</a><a>Membership</a><a>Rooms</a><a>Contact Us</a>
  </nav>
  <h1 class="abs hero-title">Swingers <span>Club</span></h1>
  <p class="abs hero-text">Velmo is one of the countries leading clubs and emphasises friendliness, fun &amp; safety for its members</p>
  <a class="abs btn hero-btn">Read More</a>
  <svg class="abs arrow" style="left:26px" width="22" height="40" viewBox="0 0 22 40"><path d="M20 2 2 20l18 18" fill="none" stroke="#fbfbfb" stroke-opacity=".6" stroke-width="2"/></svg>
  <svg class="abs arrow" style="right:26px" width="22" height="40" viewBox="0 0 22 40"><path d="m2 2 18 18L2 38" fill="none" stroke="#fbfbfb" stroke-opacity=".6" stroke-width="2"/></svg>
</header>

<section class="welcome">
  <h1>WELCOME TO VELM<span>O</span></h1>
  <p class="welcome-text">It is with regret that we have to increase some of our charges, this is due, in the main, to increased running costs for the club. Over the years I have absorbed increases but now have to pass this on to you all. This has been a difficult decision and has not been an easy one, I want to offer value for money and feel we do that for you all. Crash will be £10 per person (places allocated first come, first served @ 1.40am)</p>

  <div class="feature" style="left:112px">
    <svg width="52" height="52" viewBox="0 0 52 52"><path d="M6 26 26 6h18v18L24 44z" fill="#ec1f27"/><circle cx="36" cy="14" r="3.5" fill="#fbfbfb"/><text x="22" y="32" font-family="Roboto,sans-serif" font-size="16" font-weight="700" fill="#fbfbfb" transform="rotate(-45 22 28)">$</text></svg>
    <h3>Membership Fees</h3>
    <p>New members (Couples and Single guys) - (annual) £30, this now includes the next 2 visits half price. (Single Girls membership</p>
    <a class="more">Read More</a>
  </div>
  <div class="feature is-red" style="left:451px">
    <svg width="52" height="52" viewBox="0 0 52 52" fill="none" stroke="#fbfbfb" stroke-width="2.5"><rect x="6" y="8" width="40" height="28" stroke-dasharray="4 3"/><circle cx="16" cy="40" r="5"/><circle cx="36" cy="40" r="5"/><path d="M19 36 34 18M33 36 18 18"/></svg>
    <h3>Membership Discounts</h3>
    <p>We discount entry and membership to support Her Majesty's Forces (serving and retired), we are now happy to extend this discount</p>
    <a class="more">Read More</a>
  </div>
  <div class="feature" style="left:782px">
    <svg width="52" height="52" viewBox="0 0 52 52"><path d="M8 10h14l-1 10a6 6 0 0 1-12 0z" fill="#ec1f27"/><path d="M15 26v14M10 40h10" stroke="#ec1f27" stroke-width="2.5"/><path d="M30 14h14l-1 10a6 6 0 0 1-12 0z" fill="#ec1f27"/><path d="M37 30v14M32 44h10" stroke="#ec1f27" stroke-width="2.5"/></svg>
    <h3>Alcohol / Drinks</h3>
    <p>Please bring your own alcoholic drinks, which we will put behind the bar (chilled as necessary) and serve to you.</p>
    <a class="more">Read More</a>
  </div>
</section>

<section class="about">
  <div class="about-bg" role="img" aria-label="Red-tinted photo of a club lounge room"></div>
  <div class="about-card">
    <div class="about-photo" role="img" aria-label="Photo of a warmly lit bedroom suite with wall art and lamps"></div>
    <div class="about-body">
      <h2>Velmo :: A great place to meet and play!</h2>
      <p>We are the best in the North East, and have recently been voted No 2 club in the UK.<br>We have retained the coveted title of No 1 Friendliest club in the UK (in joint 1st place with our great friends "The Red Lantern", London).<br>This prestigious award has been given to us by a panel of "mystery voters" (swingers, singles &amp; couples) working with the publication called "Nightlife Review" a copy of which is available in reception.</p>
      <h4>We have:</h4>
      <ul class="facilities">
        <li>hot tub,</li><li>private playrooms,</li><li>dark room,</li>
        <li>sauna,</li><li>Velvet Dungeon,</li><li>Amsterdam room and more</li>
        <li>steam room,</li><li>group rooms,</li>
      </ul>
      <a class="btn about-btn">Read More ›</a>
    </div>
  </div>
</section>

<section class="news">
  <h2 style="left:97px;top:88px">Recent Blog</h2>
  <div class="abs" style="left:548px;top:92px;font-size:20px">‹ ›</div>
  <h2 style="left:778px;top:88px">Our Products</h2>

  <article class="post" style="top:158px">
    <div class="post-photo" style="background:linear-gradient(135deg,#8a5a3a,#4a2a1a)" role="img" aria-label="Photo of a club bedroom"></div>
    <div>
      <h3>Nulla at diam ornare, aliquam urna</h3>
      <div class="date">April 25, 2017</div>
      <p>Nulla at diam ornare, aliquam urna vel, commodo urna. Nam id risus a est luctus consectetur quis eget libero. Suspendisse potenti.</p>
      <a class="more">Read More +</a>
    </div>
  </article>
  <article class="post" style="top:339px">
    <div class="post-photo" style="background:linear-gradient(135deg,#3a6aa8,#c04a8a 60%,#e0a040)" role="img" aria-label="Photo of guests at a party under colourful lights"></div>
    <div>
      <h3>Nulla at diam ornare, aliquam urna</h3>
      <div class="date">April 25, 2017</div>
      <p>Nulla at diam ornare, aliquam urna vel, commodo urna. Nam id risus a est luctus consectetur quis eget libero. Suspendisse potenti.</p>
      <a class="more">Read More +</a>
    </div>
  </article>

  <div class="product" role="img" aria-label="Branded white t-shirt on a hanger against a wooden wall">
    <div class="shirt">
      <div class="brand">Velmo</div>
      <p>Sed ut perspiciatis unde omnis iste natus error sit voluptatem accusan</p>
      <a class="btn shop-btn">Shop Now!</a>
    </div>
    <div class="market">tradeva</div>
  </div>
</section>

<section class="price">
  <div class="price-bg" role="img" aria-label="Red-tinted photo of friends laughing with drinks"></div>
  <h2>Price Increases (from April 2017)</h2>
  <p>Crash will be £10 per person (places allocated first come, first served @ 1.40am) Corkage will be £1 per person ( we will now have available lemons &amp; limes)</p>
  <div class="abs email">email</div>
  <a class="abs join">Join Now!</a>
</section>

<footer class="site-footer">
  <h5 style="left:97px">Quick Link</h5>
  <ul class="links">
    <li>Home</li><li>Diary</li><li>Theme Parties</li><li>TV/TG and Admirers</li><li>Membership</li><li>FAQs</li><li>Rooms</li><li>Contact Us</li>
  </ul>
  <h5 style="left:316px">Contact Us</h5>
  <div class="contact">
    <div><svg width="14" height="18" viewBox="0 0 14 18"><path d="M7 0a7 7 0 0 0-7 7c0 5 7 11 7 11s7-6 7-11a7 7 0 0 0-7-7z" fill="#fbfbfb"/><circle cx="7" cy="7" r="2.5" fill="#1c1c1c"/></svg><span>Velmo<br>14 Harbour Row, Tynefield UK</span></div>
    <div><svg width="14" height="14" viewBox="0 0 24 24"><path fill="#fbfbfb" d="M6.6 10.8a15.1 15.1 0 0 0 6.6 6.6l2.2-2.2c.3-.3.7-.4 1-.2 1.1.4 2.3.6 3.6.6.6 0 1 .4 1 1V20c0 .6-.4 1-1 1A17 17 0 0 1 3 4c0-.6.4-1 1-1h3.5c.6 0 1 .4 1 1 0 1.3.2 2.5.6 3.6.1.3 0 .7-.2 1z"/></svg><span>Phone : 01632 960418</span></div>
    <div><svg width="14" height="12" viewBox="0 0 14 12"><rect width="14" height="12" fill="#fbfbfb"/><path d="m0 0 7 6 7-6" fill="none" stroke="#1c1c1c" stroke-width="1.5"/></svg><span>Email : velmoswingers@example.co.uk</span></div>
  </div>
  <div class="abs brand footer-logo">Velmo</div>
  <h5 style="left:634px">Get a Quote</h5>
  <p class="abs quote-text">Lorem ipsum dolor sit amet, consectetur adipiscing elit, sed do eiusmod tempor incididunt ut labore et dolore magna aliqua. Ut enim ad minim veniam,</p>
  <div class="field" style="left:634px;top:148px;width:228px">Name</div>
  <div class="field" style="left:877px;top:148px;width:224px">E - Mail</div>
  <div class="field" style="left:634px;top:200px;width:228px">Phone No</div>
  <a class="signup">Signup Now</a>
</footer>

<div class="bottom-bar">
  <div class="abs copy">© 2017 velmo-example.co.uk. All Rights Reserved.</div>
  <div class="abs social"><span></span><span></span><span></span><span></span></div>
</div>

</body>
</html>
```